Aviation Law Firm Needs Envelope Design

The envelope design must be EYE CATCHING and sexy, yet very professional. The information in the return address should be in the upper left hand corner and read:
The Marrow Law Firm
P.O. Box 8175
Lakeland, Florida 33912

The word: "ADVERTISEMENT" must appear on the front of the envelope in some fashion.

The colors should compliment the letterhead image (attached). However, I would like for the envelope to remain white or light colored in the upper right hand corner so that the post office can read any stamps, etc.

Target Market(s)

Pilots; Legal Clients

Industry/Entity Type

Law Firm

Font styles to use
Serif
Sans Serif

Colors
191919
fbee3e
ffffff

Requirements
Must have
• Must capture the use of the entire envelope, BUT leave space for receiver's address and post office stamps, etc.

```html
<!DOCTYPE html>
<html lang="en">
<head>
<meta charset="utf-8">
<title>The Marrow Law Firm – Envelope</title>
<link href="https://fonts.googleapis.com/css2?family=Arimo:ital,wght@0,400;0,700;1,700&display=swap" rel="stylesheet">
<style>
  :root {
    --ink: #191919;
    --sunflower: #fbee3e;
    --paper: #ffffff;
    --backdrop: #e9e9ea;
    --faint: #f6f1cf;
  }
  * { margin: 0; padding: 0; box-sizing: border-box; }
  html, body { width: 1200px; height: 800px; overflow: hidden; }
  body {
    background: var(--backdrop);
    font-family: "Arimo", Arial, sans-serif;
    color: var(--ink);
    position: relative;
  }
  .envelope {
    position: absolute;
    left: 200px;
    width: 800px;
    height: 350px;
    background: var(--paper);
    box-shadow: 0 2px 8px rgba(0,0,0,0.12);
    overflow: hidden;
  }
  .envelope--back { top: 30px; }
  .envelope--front { top: 420px; }
  .envelope svg.artwork {
    position: absolute; inset: 0; width: 100%; height: 100%;
  }
  .flap-title {
    position: absolute;
    top: 26px; left: 0; width: 760px;
    text-align: center;
    font-size: 20px;
    letter-spacing: 3px;
  }
  .flap-mark {
    position: absolute;
    top: 170px; left: 0; width: 800px;
    display: flex; align-items: center; justify-content: center; gap: 14px;
    color: var(--faint);
    font-size: 30px; font-weight: 700; letter-spacing: 2px;
  }
  .flap-mark .dot {
    width: 34px; height: 34px; border-radius: 50%; background: var(--faint);
  }
  .firm-mark {
    position: absolute;
    top: 178px; left: 48px;
    display: flex; align-items: center; gap: 10px;
    font-size: 15px; font-weight: 700; letter-spacing: 1px;
  }
  .firm-mark .dot {
    width: 30px; height: 30px; border-radius: 50%; background: var(--sunflower);
  }
  .return-address {
    position: absolute;
    top: 40px; left: 520px;
    font-size: 17px; font-weight: 700; line-height: 1.35;
    letter-spacing: 2.5px;
    font-style: normal;
  }
  .advertisement {
    position: absolute;
    right: 60px; bottom: 8px;
    font-size: 28px; font-weight: 700; font-style: italic;
    letter-spacing: 8px;
  }
</style>
</head>
<body>

  <section class="envelope envelope--back" aria-label="Envelope back">
    <svg class="artwork" viewBox="0 0 800 350" aria-hidden="true">
      <polygon points="0,0 800,0 800,25 755,90 0,90" fill="var(--sunflower)"/>
    </svg>
    <p class="flap-title">The Marrow Law Firm</p>
    <div class="flap-mark"><span class="dot"></span>The Marrow Law Firm</div>
  </section>

  <section class="envelope envelope--front" aria-label="Envelope front">
    <svg class="artwork" viewBox="0 0 800 350" aria-hidden="true">
      <path d="M0,228 C180,262 380,285 580,296 C700,302 760,308 800,330 L800,350 L0,350 Z" fill="var(--sunflower)"/>
      <path d="M0,228 C180,262 380,285 580,296 C700,302 760,308 800,330" fill="none" stroke="var(--ink)" stroke-width="5"/>
    </svg>
    <div class="firm-mark"><span class="dot"></span>The Marrow Law Firm</div>
    <address class="return-address">
      The Marrow Law Firm<br>
      P.O. Box 8175<br>
      Lakeland, Florida 33912
    </address>
    <p class="advertisement">ADVERTISEMENT</p>
  </section>

</body>
</html>
```